Tovimar Community Development Planning New web site

Design a new web site. I have a budget of $1,500.00.
Attached on PowerPoint is a complete site plan. Home page and linked pages.
10 - 12 pages. All copy and photos will be supplied. (300dpi)
I have shown them the concept which they like.
No data bases required. Home page with animations dissolving.
They former web site has been taken down. They have been in business 30 years in New Jersey
Colors teal blues and greens
There will be a new logo)being designed)
The text in home page copy will give you a detailed story what they are all about.

files have been approved for Tovimar, Inc.   Brenton is the designer

```html
<!DOCTYPE html>
<html lang="en">
<head>
<meta charset="utf-8">
<title>Tovimar, Inc. | City Planning Firm</title>
<link rel="stylesheet" href="https://fonts.googleapis.com/css2?family=Open+Sans:wght@300;400;600;700&display=swap">
<style>
:root{
  --teal:#17758f;
  --teal-dark:#0e5a70;
  --teal-text:#1d8aa6;
  --green:#6aac3e;
  --green-dark:#579131;
  --ink:#333;
  --body:#666;
  --muted:#999;
  --rule:#ddd;
  --band:#f1f1f1;
  --footer:#2e2e2e;
  --footer-base:#222;
  --white:#fff;
}
*{box-sizing:border-box;margin:0;padding:0}
html,body{width:1200px;height:3470px;overflow:hidden}
body{font-family:"Open Sans",Arial,sans-serif;color:var(--body);background:var(--white);font-size:11px;line-height:1.6}
.wrap{width:1000px;margin:0 auto;position:relative;height:100%}
section,header,footer{position:relative;overflow:hidden}

/* top bar */
.topbar{height:52px;font-size:11px;color:var(--muted)}
.topbar .wrap{display:flex;align-items:center;justify-content:space-between}
.topbar .left{display:flex;gap:22px;align-items:center}
.topbar .right{display:flex;gap:8px;align-items:center}
.dot-social{width:11px;height:11px;border-radius:50%;background:var(--green)}
.topbar .links{margin-left:12px}

/* nav */
.mainnav{height:87px;background:var(--teal)}
.mainnav .wrap{display:flex;align-items:stretch;justify-content:space-between}
.brand{display:flex;align-items:center;gap:12px;color:var(--white)}
.brand-mark{width:34px;height:34px;background:var(--white)}
.brand-name{font-size:24px;font-weight:700;line-height:1}
.brand-tag{font-size:11px;color:#cfe7ee;margin-top:4px;padding-left:80px}
.menu{display:flex;list-style:none}
.menu li{display:flex;align-items:center;padding:0 22px;color:var(--white);font-size:13px}
.menu li.active{background:var(--teal-dark)}

/* hero */
.hero{height:376px}
.hero-photo{position:absolute;inset:0;background:linear-gradient(90deg,#8b97a2 0%,#aab4bd 35%,#c9ced2 62%,#b7b3ad 80%,#8d8a86 100%)}
.hero-veil{position:absolute;left:300px;top:120px;width:600px;height:170px;background:radial-gradient(ellipse at center,rgba(255,255,255,.85),rgba(255,255,255,0) 70%)}
.hero-copy{position:absolute;left:0;right:0;top:142px;text-align:center;padding-right:20px}
.hero-copy .l1{font-size:22px;color:#2c3a40;font-weight:600}
.hero-copy .l2{font-size:24px;color:#4aa37c;font-weight:300;letter-spacing:.5px;line-height:1.2}
.hero-copy .l3{font-size:42px;color:var(--teal-text);font-weight:400;line-height:1.2}
.arrow{position:absolute;top:165px;width:40px;height:48px;background:rgba(20,20,20,.75);display:flex;align-items:center;justify-content:center}
.arrow.prev{left:100px}.arrow.next{right:100px}

/* welcome */
.welcome{height:303px;text-align:center}
.welcome h1{font-size:30px;font-weight:400;color:var(--ink);padding-top:70px;margin-bottom:26px}
.welcome p{font-size:10.5px;color:var(--muted);margin-bottom:16px}

/* services */
.services{height:289px;background:var(--band)}
.services .wrap{display:flex;justify-content:space-between;padding:55px 30px 0}
.service{width:200px;text-align:center}
.service .icon{width:52px;height:52px;background:var(--green);margin:0 auto 14px;display:flex;align-items:center;justify-content:center;border-radius:3px}
.service h3{font-size:21px;font-weight:400;color:var(--teal-text);margin-bottom:6px}
.service p{font-size:10px;color:var(--muted);line-height:1.5}
.service .more{display:block;margin-top:12px;color:var(--teal-text);font-size:10px;font-weight:600}

/* results */
.results{height:400px}
.results-art{position:absolute;left:115px;top:20px;width:390px;height:318px;background:radial-gradient(ellipse at 55% 45%,#d9d2c8 0%,#c8bfb1 40%,#eae7e2 75%,#fff 100%)}
.results-body{position:absolute;left:549px;top:80px;width:550px}
.section-title{font-size:28px;font-weight:400;color:var(--ink);display:flex;align-items:center;gap:14px}
.section-title::after{content:"";flex:1;height:1px;background:var(--rule)}
.facts{display:grid;grid-template-columns:270px 260px;gap:28px 20px;margin-top:36px;padding-left:16px}
.fact{display:flex;gap:14px}
.fact svg{flex:none}
.fact p{font-size:11px;color:var(--body);line-height:1.5}

/* memberships */
.memberships{height:320px}
.memberships .section-title{position:absolute;left:95px;top:38px;width:470px;font-size:26px}
.memberships .text{position:absolute;left:95px;top:100px;width:470px}
.memberships .text p{margin-bottom:32px;font-size:10.5px}
.partners{position:absolute;left:607px;top:68px;width:490px;display:grid;grid-template-columns:1fr 1fr;gap:26px 30px}
.partner{height:80px;border-radius:4px}
.p1{background:#4b7fb7;width:200px}
.p2{background:#2d2d2d;width:80px;border-radius:50%;justify-self:center}
.p3{background:#3aa0a6;width:200px}
.p4{background:#3a5f95;width:200px;height:56px;align-self:center}

/* lottery */
.lottery{height:470px}
.lottery-art{position:absolute;left:160px;top:53px;width:275px;height:388px;background:radial-gradient(ellipse at 50% 40%,#e8c86a 0%,#c9a03a 45%,#8a6b22 75%,#fff 100%)}
.lottery-body{position:absolute;left:545px;top:88px;width:553px}
.lottery-body .section-title{font-size:27px}
.lottery-body p{font-size:10.5px;color:var(--body);margin-top:14px;line-height:1.6}

/* testimonial */
.testimonial{height:232px;text-align:center;color:var(--white)}
.testimonial-photo{position:absolute;inset:0;background:linear-gradient(180deg,#c89a5c 0%,#7a5a3e 38%,#2d2a2c 70%,#1b1d22 100%)}
.testimonial-photo::after{content:"";position:absolute;inset:0;background:rgba(10,20,30,.35)}
.testimonial .inner{position:relative;padding-top:12px}
.quote-badge{width:62px;height:62px;border-radius:50%;background:var(--white);margin:0 auto 16px;display:flex;align-items:center;justify-content:center}
.testimonial p{font-size:12.5px;width:1000px;margin:0 auto;line-height:1.6}
.testimonial .who{display:block;margin-top:12px;font-size:11.5px}
.dots{display:flex;justify-content:center;gap:6px;margin-top:8px}
.dots span{width:12px;height:12px;border-radius:50%;border:2px solid var(--green)}
.dots span.on{background:var(--green)}

/* recent work */
.work{height:598px}
.work h2{text-align:center;font-size:27px;font-weight:400;color:var(--ink);padding-top:80px}
.filters{position:absolute;left:101px;top:150px;display:flex;gap:8px}
.filters span{padding:4px 10px;border:1px solid var(--rule);font-size:11px;color:var(--body);background:var(--white)}
.filters span.on{background:var(--green);color:var(--white);border-color:var(--green);font-weight:600}
.gallery{position:absolute;left:101px;top:211px;width:998px;display:grid;grid-template-columns:repeat(4,243px);grid-auto-rows:184px;gap:8px 8px}
.tile{display:block}
.t1{background:linear-gradient(135deg,#e8dfc9,#b9a984)}
.t2{background:linear-gradient(180deg,#9ec2e0,#7b8a6a 60%,#9a8a72)}
.t3{background:linear-gradient(180deg,#a9c7e4,#8a6e4f 55%,#6f7d4a)}
.t4{background:linear-gradient(180deg,#b8d0e8,#c2a27a 55%,#b79b77)}
.t5{background:linear-gradient(180deg,#7fa7d6,#6e6e72 55%,#4f5a3c)}
.t6{background:linear-gradient(180deg,#b6cde4,#8d8579 55%,#5e6b48)}
.t7{background:linear-gradient(180deg,#c9d6e1,#9a6b44 50%,#7a5638)}
.t8{background:linear-gradient(160deg,#2f6fb8,#6ba6e0 50%,#1d4f8f)}

/* footer */
.site-footer{height:298px;background:var(--footer);color:#bbb}
.site-footer .wrap{display:grid;grid-template-columns:309px 232px 225px 234px;padding-top:20px}
.site-footer h4{color:var(--white);font-size:14px;font-weight:400;margin-bottom:14px}
.blog-item{font-size:10px;line-height:1.5;margin-bottom:10px;width:230px}
.blog-item time{display:block;color:var(--green)}
.view-all{display:block;text-align:right;width:230px;font-size:10px;color:var(--white);text-decoration:underline}
.contact li{list-style:none;display:flex;gap:8px;font-size:10px;margin-bottom:10px;width:200px}
.contact svg{flex:none;margin-top:2px}
.socials{display:flex;gap:8px;margin-top:6px}
.socials span{width:14px;height:14px;background:#ddd;border-radius:2px}
.newsletter p{font-size:10px;width:200px}
.field{margin-top:12px;width:196px;height:24px;background:#4a4a4a;border:1px solid #555;color:#999;font-size:10px;padding:4px 8px}
.btn{display:flex;gap:10px;margin-top:10px;align-items:flex-start}
.btn span{background:var(--green);color:var(--white);font-size:10px;padding:4px 8px;font-weight:600}
.btn small{font-size:9px;width:120px;line-height:1.4}
.stream{display:grid;grid-template-columns:repeat(3,72px);grid-auto-rows:56px;gap:4px}
.s1{background:linear-gradient(135deg,#6f9b3a,#2f4d1c)}
.s2{background:linear-gradient(135deg,#9bbd4a,#4e6b24)}
.s3{background:linear-gradient(135deg,#d7c23c,#6d8a2b)}
.s4{background:linear-gradient(135deg,#7c3f82,#2b1b4a)}
.s5{background:linear-gradient(135deg,#c44d2f,#3b1c28)}
.s6{background:linear-gradient(135deg,#3d6e3a,#1d2f1a)}
.s7{background:linear-gradient(135deg,#5aa03a,#26461c)}
.s8{background:linear-gradient(135deg,#2f5fa0,#17283f)}
.s9{background:linear-gradient(135deg,#a8c95a,#4d6a25)}
.base{height:45px;background:var(--footer-base);text-align:center;font-size:10px;color:#777;line-height:45px}
</style>
</head>
<body>

<header class="topbar">
  <div class="wrap">
    <div class="left">
      <span>April 16, 2014</span>
      <span>
        <svg width="11" height="11" viewBox="0 0 12 12" style="vertical-align:-1px"><circle cx="6" cy="6" r="5" fill="none" stroke="#999"/><path d="M1 6h10M6 1c-2 3-2 7 0 10M6 1c2 3 2 7 0 10" fill="none" stroke="#999" stroke-width=".8"/></svg>
        Language
      </span>
    </div>
    <div class="right">
      <span class="dot-social"></span><span class="dot-social"></span><span class="dot-social"></span>
      <span class="links">Subscribe &nbsp;|&nbsp; Login</span>
    </div>
  </div>
</header>

<nav class="mainnav">
  <div class="wrap">
    <div class="brand">
      <span class="brand-mark"></span>
      <div>
        <div class="brand-name">Tovimar, Inc.</div>
        <div class="brand-tag">City Planning Firm</div>
      </div>
    </div>
    <ul class="menu">
      <li class="active">Home</li>
      <li>Our Company</li>
      <li>Housing Rehab Application</li>
      <li>Affordable Application</li>
      <li>Contact Us</li>
    </ul>
  </div>
</nav>

<section class="hero">
  <div class="hero-photo" role="img" aria-label="City skyline aerial view with planners reviewing a white architectural model"></div>
  <div class="hero-veil"></div>
  <div class="hero-copy">
    <div class="l1">we implement local programs</div>
    <div class="l2">TO BENEFIT PEOPLE SEEKING ACCESS TO</div>
    <div class="l3">AFFORDABLE HOUSING</div>
  </div>
  <div class="arrow prev"><svg width="14" height="22" viewBox="0 0 14 22"><path d="M11 2 3 11l8 9" fill="none" stroke="#fff" stroke-width="2.5"/></svg></div>
  <div class="arrow next"><svg width="14" height="22" viewBox="0 0 14 22"><path d="M3 2l8 9-8 9" fill="none" stroke="#fff" stroke-width="2.5"/></svg></div>
</section>

<section class="welcome">
  <div class="wrap">
    <h1>Welcome to Tovimar Inc.</h1>
    <p>Tovimar, Inc. is a city planning firm that specializes in community development and housing rehabilitation program planning, design and implementation. We have over twenty years of experience in<br>developing and administering income based home housing and programs in accordance with federal housing and urban development rules and state council on affordable housing<br>guidelines and regulations.</p>
    <p>In addition, our firm is capable of providing the technical and administrative assistance our clients require for implementation of their income based housing programs. Hallard Pryce Associates is one<br>of the most experienced urban planning firms in New Jersey, with over forty years of practice as consulting planners.</p>
  </div>
</section>

<section class="services">
  <div class="wrap">
    <div class="service">
      <div class="icon"><svg width="26" height="26" viewBox="0 0 26 26"><circle cx="11" cy="11" r="7" fill="none" stroke="#fff" stroke-width="2.5"/><path d="M16 16l7 7" stroke="#fff" stroke-width="3"/></svg></div>
      <h3>Research</h3>
      <p>Nam quis dui vitae odio pulvinar scelerisque nec quis risus. Morbi at condimentum enim. Phasellus sollicitudin et ligula sit amet cursus. Proin volutpat adipiscing aliquet sit amet mattis.</p>
      <span class="more">View more ›</span>
    </div>
    <div class="service">
      <div class="icon"><svg width="26" height="26" viewBox="0 0 26 26"><rect x="4" y="4" width="18" height="18" fill="none" stroke="#fff" stroke-width="2.2"/><path d="M8 18 18 8" stroke="#fff" stroke-width="2.5"/></svg></div>
      <h3>Design</h3>
      <p>Nam quis dui vitae odio pulvinar scelerisque nec quis risus. Morbi at condimentum enim. Phasellus sollicitudin et ligula sit amet cursus. Proin volutpat adipiscing aliquet sit amet mattis.</p>
      <span class="more">View more ›</span>
    </div>
    <div class="service">
      <div class="icon"><svg width="26" height="26" viewBox="0 0 26 26"><path d="M3 23V11l10-7 10 7v12z" fill="none" stroke="#fff" stroke-width="2.2"/><rect x="10" y="15" width="6" height="8" fill="#fff"/></svg></div>
      <h3>Construction</h3>
      <p>Nam quis dui vitae odio pulvinar scelerisque nec quis risus. Morbi at condimentum enim. Phasellus sollicitudin et ligula sit amet cursus. Proin volutpat adipiscing aliquet sit amet mattis.</p>
      <span class="more">View more ›</span>
    </div>
    <div class="service">
      <div class="icon"><svg width="26" height="26" viewBox="0 0 26 26"><path d="M6 3h5l2 6-3 2a12 12 0 0 0 5 5l2-3 6 2v5c0 1-1 2-2 2C11 22 4 15 4 5c0-1 1-2 2-2z" fill="#fff"/></svg></div>
      <h3>Support</h3>
      <p>Nam quis dui vitae odio pulvinar scelerisque nec quis risus. Morbi at condimentum enim. Phasellus sollicitudin et ligula sit amet cursus. Proin volutpat adipiscing aliquet sit amet mattis.</p>
      <span class="more">View more ›</span>
    </div>
  </div>
</section>

<section class="results">
  <div class="results-art" role="img" aria-label="Cutaway illustration of a house with an energy efficiency rating chart"></div>
  <div class="results-body">
    <h2 class="section-title">WE GET RESULTS</h2>
    <div class="facts">
      <div class="fact">
        <svg width="22" height="22" viewBox="0 0 22 22"><rect width="22" height="22" rx="3" fill="#17758f"/><path d="M14 7c-1-1-5-1-5 1.5S14 10 14 13s-4 2.5-5 1.5M11 5v12" fill="none" stroke="#fff" stroke-width="1.6"/></svg>
        <p>Tovimar designs income based programs to be supported by federal placement lotteries state funding.</p>
      </div>
      <div class="fact">
        <svg width="22" height="22" viewBox="0 0 22 22"><path d="M2 11 11 3l9 8h-3v9H5v-9z" fill="#17758f"/></svg>
        <p>We implement local programs to benefit people seeking access to affordable housing.</p>
      </div>
      <div class="fact">
        <svg width="22" height="22" viewBox="0 0 22 22"><circle cx="11" cy="11" r="10" fill="#17758f"/><path d="M6 11l4 4 6-8" fill="none" stroke="#fff" stroke-width="2"/></svg>
        <p>Our experienced staff screen applicants for local affordable housing. We pre-qualify persons who have applied for housing rehabilitation.</p>
      </div>
      <div class="fact">
        <svg width="22" height="22" viewBox="0 0 22 22"><path d="M3 16a8 8 0 0 1 16 0z" fill="#17758f"/><rect x="1" y="16" width="20" height="3" fill="#17758f"/></svg>
        <p>Through local housing rehabilitation programs, our experience construction inspectors determine what improvements are required at eligible units based on local building codes and health and safety issues.</p>
      </div>
    </div>
  </div>
</section>

<section class="memberships">
  <h2 class="section-title">OUR MEMBERSHIPS</h2>
  <div class="text">
    <p>Fusce euismod dolor vel odio adipiscing, vitae placerat mi placerat. Proin interdum imperdiet hendrerit. Etiam egestas eros in odio mattis, in imperdiet tellus tincidunt. Nunc quis cursus eros, venenatis massa. Class aptent taciti sociosqu ad litora torquent per conubia nostra, per inceptos himenaeos.</p>
    <p>Fusce euismod dolor vel odio adipiscing, vitae placerat mi placerat. Proin interdum imperdiet hendrerit. Etiam egestas eros in odio mattis, in imperdiet tellus tincidunt. Nunc quis cursus eros, venenatis massa. Class aptent taciti sociosqu ad litora torquent per conubia nostra, per inceptos himenaeos.</p>
  </div>
  <div class="partners">
    <span class="partner p1"></span>
    <span class="partner p2"></span>
    <span class="partner p3"></span>
    <span class="partner p4"></span>
  </div>
</section>

<section class="lottery">
  <div class="lottery-art" role="img" aria-label="Golden lottery ball drum on a stand"></div>
  <div class="lottery-body">
    <h2 class="section-title">HOW YOUR LOTTERY WORKS</h2>
    <p>Vivamus id pulvinar elit. Duis in est nec velit fringilla fermentum. Phasellus sollicitudin massa ac urna aliquam, in malesuada mi imperdiet. Phasellus varius nunc in nisi iaculis condimentum. Suspendisse potenti. Curabitur fermentum tortor lectus, eget interdum lacus vulputate ac. Sed eu ornare sem. Nam quis dui vitae odio pulvinar scelerisque nec quis risus. Morbi at condimentum enim. Phasellus sollicitudin at ligula sit amet cursus. Phasellus adipiscing sed justo sit amet mattis. Proin et arcu nulla. Donec iaculis, massa vel pharetra iaculis, enim libero scelerisque nunc, id sollicitudin ante ante sit amet enim. Phasellus tincidunt accumsan eros quis mattis lorem volutpat laoreet.</p>
    <p>Fusce euismod dolor vel odio adipiscing, vitae placerat mi placerat. Proin interdum imperdiet hendrerit. Etiam egestas eros in odio mattis, in imperdiet tellus tincidunt. Nunc quis cursus eros, venenatis massa. Class aptent taciti sociosqu ad litora torquent per conubia nostra, per inceptos himenaeos. Integer id elit pretium, tempor mauris sed, facilisis elit. Pellentesque bibendum, magna et suscipit consectetur, enim nisi.</p>
  </div>
</section>

<section class="testimonial">
  <div class="testimonial-photo" role="img" aria-label="City skyline at dusk with light trails on a highway"></div>
  <div class="inner">
    <div class="quote-badge"><svg width="24" height="20" viewBox="0 0 24 20"><path d="M2 20V11C2 5 5 1 10 0v4c-3 1-4 3-4 6h4v10zm12 0V11c0-6 3-10 8-11v4c-3 1-4 3-4 6h4v10z" fill="#6aac3e"/></svg></div>
    <p>Vivamus id pulvinar elit. Duis in est nec velit fringilla fermentum. Phasellus sollicitudin massa ac urna aliquam, in malesuada mi imperdiet. Phasellus varius nunc in nisi<br>iaculis condimentum. Suspendisse potenti. Curabitur fermentum tortor lectus, eget interdum lacus vulputate ac. Sed eu ornare sem. Nam quis dui vitae odio pulvinar<br>scelerisque nec quis risus.</p>
    <span class="who">Morbi convallis</span>
    <div class="dots"><span class="on"></span><span></span><span></span></div>
  </div>
</section>

<section class="work">
  <h2>OUR RECENT WORK</h2>
  <div class="filters">
    <span class="on">Show All</span><span>Commercial</span><span>Residential</span><span>Awesome</span><span>Artistic</span>
  </div>
  <div class="gallery">
    <span class="tile t1" role="img" aria-label="Bright renovated kitchen interior"></span>
    <span class="tile t2" role="img" aria-label="Row of suburban houses"></span>
    <span class="tile t3" role="img" aria-label="Brick townhouses along a street"></span>
    <span class="tile t4" role="img" aria-label="New homes under construction on a dirt road"></span>
    <span class="tile t5" role="img" aria-label="Two storey family home at dusk"></span>
    <span class="tile t6" role="img" aria-label="Residential houses with green lawns"></span>
    <span class="tile t7" role="img" aria-label="Brick apartment building under construction"></span>
    <span class="tile t8" role="img" aria-label="Glass office tower facade"></span>
  </div>
</section>

<footer class="site-footer">
  <div class="wrap">
    <div>
      <h4>Latest Blog</h4>
      <div class="blog-item">Aenean malesuada ullamcorper mi amet tempor felis aliquet at. Aenean vulputate risus sit amet quam.<time>24 Jan 2014</time></div>
      <div class="blog-item">Aenean malesuada ullamcorper mi amet tempor felis aliquet at. Aenean vulputate risus sit amet quam.<time>24 Jan 2014</time></div>
      <span class="view-all">view all »</span>
    </div>
    <div>
      <h4>Contact Info</h4>
      <ul class="contact">
        <li><svg width="9" height="12" viewBox="0 0 9 12"><path d="M4.5 0A4.5 4.5 0 0 0 0 4.5C0 8 4.5 12 4.5 12S9 8 9 4.5A4.5 4.5 0 0 0 4.5 0z" fill="#ccc"/><circle cx="4.5" cy="4.5" r="1.6" fill="#2e2e2e"/></svg>418 Kestrel Avenue, Suite 2, Ridgefield NJ 07657</li>
        <li><svg width="10" height="10" viewBox="0 0 26 26"><path d="M6 3h5l2 6-3 2a12 12 0 0 0 5 5l2-3 6 2v5c0 1-1 2-2 2C11 22 4 15 4 5c0-1 1-2 2-2z" fill="#ccc"/></svg>(201) 555-0147</li>
        <li><svg width="11" height="9" viewBox="0 0 11 9"><rect x=".5" y=".5" width="10" height="8" fill="none" stroke="#ccc"/><path d="M.5.5l5 4 5-4" fill="none" stroke="#ccc"/></svg>info@tovimar.com</li>
      </ul>
      <div class="socials"><span></span><span></span><span></span><span></span></div>
    </div>
    <div class="newsletter">
      <h4>Newsletter</h4>
      <p>Ut et neque nec purus suscipit leo, ut sollicitudin lacinia vulputate ante. Proin at neque sodales.</p>
      <div class="field">Enter email</div>
      <div class="btn"><span>Submit</span><small>Ut et neque nec purus suscipit leo, ut sollicitudin.</small></div>
    </div>
    <div>
      <h4>Photo Stream</h4>
      <div class="stream">
        <span class="s1" role="img" aria-label="Green foliage photo"></span>
        <span class="s2" role="img" aria-label="Meadow photo"></span>
        <span class="s3" role="img" aria-label="Yellow flowers photo"></span>
        <span class="s4" role="img" aria-label="Night city lights photo"></span>
        <span class="s5" role="img" aria-label="Sunset photo"></span>
        <span class="s6" role="img" aria-label="Forest photo"></span>
        <span class="s7" role="img" aria-label="Leaves close-up photo"></span>
        <span class="s8" role="img" aria-label="Blue evening photo"></span>
        <span class="s9" role="img" aria-label="Spring field photo"></span>
      </div>
    </div>
  </div>
</footer>
<div class="base">Copyright 2014. All rights reserved.</div>

</body>
</html>
```